Asphalt Driveway Billboard Design

We need a billboard designed for an Paving & Concrete Company in Minnesota. We want to advertise Asphalt Driveways on this billboard! Logo is uploaded below. Our website is pinecrest-paving.com for more information.

```html
<!DOCTYPE html>
<html lang="en">
<head>
<meta charset="utf-8">
<title>Pinecrest Paving – Asphalt Driveway Billboard</title>
<link href="https://fonts.googleapis.com/css2?family=Michroma&family=Montserrat:wght@600;800&family=Oswald:wght@700&display=swap" rel="stylesheet">
<style>
  :root {
    --page-bg: #f4f5f7;
    --asphalt-black: #141414;
    --brand-blue: #1b6cb8;
    --photo-deep: #173f6d;
    --photo-light: #4f8cc4;
    --curb-grey: #b9bbbe;
    --curb-line: #6f7275;
    --white: #ffffff;
    --ink: #111111;
  }
  * { margin: 0; padding: 0; box-sizing: border-box; }
  html, body {
    width: 1069px; height: 1200px; overflow: hidden;
    background: var(--page-bg);
  }
  .billboard {
    position: absolute;
    left: 34px; top: 455px;
    width: 1000px; height: 290px;
    overflow: hidden;
    box-shadow: 0 4px 10px rgba(0,0,0,0.35);
  }
  .billboard-shapes { position: absolute; inset: 0; width: 100%; height: 100%; }

  .brand-mark {
    position: absolute;
    left: 140px; top: 48px;
    width: 90px; height: 90px;
    background: var(--white);
  }
  .brand-name,
  .brand-tagline {
    position: absolute;
    left: 0; width: 370px;
    text-align: center;
    color: var(--white);
    font-family: "Montserrat", sans-serif;
    font-weight: 800;
    line-height: 1;
    white-space: nowrap;
  }
  .brand-name { top: 186px; font-size: 40px; letter-spacing: 0.01em; }
  .brand-tagline { top: 236px; font-size: 16px; letter-spacing: 0.04em; }

  .headline {
    position: absolute;
    left: 482px; top: 24px;
    color: var(--white);
    font-family: "Michroma", sans-serif;
    font-weight: 400;
    line-height: 0.86;
    white-space: nowrap;
  }
  .headline .line-one { display: block; font-size: 58px; letter-spacing: 0.01em; }
  .headline .line-two { display: block; font-size: 60px; letter-spacing: -0.02em; }

  .phone-bar {
    position: absolute;
    left: 481px; top: 136px; width: 476px; height: 57px;
    background: var(--brand-blue);
    color: var(--ink);
    font-family: "Oswald", sans-serif;
    font-weight: 700;
    font-size: 50px; line-height: 57px;
    text-align: center;
    letter-spacing: 0.04em;
  }
  .website {
    position: absolute;
    left: 481px; top: 199px; width: 476px;
    color: var(--white);
    font-family: "Montserrat", sans-serif;
    font-weight: 800;
    font-size: 25px; line-height: 28px;
    text-align: center;
    letter-spacing: 0.01em;
    white-space: nowrap;
  }
  .estimate-bar {
    position: absolute;
    left: 481px; top: 234px; width: 476px; height: 30px;
    background: var(--curb-grey);
    color: var(--ink);
    font-family: "Montserrat", sans-serif;
    font-weight: 600;
    font-size: 19px; line-height: 30px;
    text-align: center;
    letter-spacing: 0.45em;
  }
</style>
</head>
<body>
  <div class="billboard">
    <svg class="billboard-shapes" viewBox="0 0 1570 456" preserveAspectRatio="none">
      <defs>
        <linearGradient id="photoTone" x1="0" y1="0" x2="0" y2="1">
          <stop offset="0" stop-color="#4f8cc4"/>
          <stop offset="0.45" stop-color="#2a5e98"/>
          <stop offset="1" stop-color="#173f6d"/>
        </linearGradient>
      </defs>
      <rect class="photo-area" x="0" y="0" width="780" height="456" fill="url(#photoTone)" role="img" aria-label="Photo of a house with a freshly paved asphalt driveway, tinted blue"/>
      <path class="blue-sweep" d="M640 0 Q500 228 590 456 L780 456 L780 0 Z" fill="var(--brand-blue)"/>
      <path class="white-stripe" d="M652 0 Q515 228 603 456 L780 456 L780 0 Z" fill="var(--white)"/>
      <path class="curb-band" d="M668 0 Q535 228 618 456 L780 456 L780 0 Z" fill="var(--curb-grey)"/>
      <g class="curb-joints" stroke="var(--curb-line)" stroke-width="4">
        <line x1="600" y1="95" x2="720" y2="95"/>
        <line x1="580" y1="170" x2="700" y2="170"/>
        <line x1="575" y1="250" x2="700" y2="250"/>
        <line x1="585" y1="330" x2="700" y2="330"/>
        <line x1="600" y1="400" x2="720" y2="400"/>
      </g>
      <path class="asphalt-panel" d="M712 -4 Q585 228 692 460 L1574 460 L1574 -4 Z" fill="var(--asphalt-black)" stroke="var(--white)" stroke-width="5"/>
    </svg>

    <div class="brand-mark"></div>
    <div class="brand-name">PINECREST</div>
    <div class="brand-tagline">— PAVING &amp; CONCRETE —</div>

    <h1 class="headline">
      <span class="line-one">ASPHALT</span>
      <span class="line-two">DRIVEWAY</span>
    </h1>
    <div class="phone-bar">763-555-0148</div>
    <div class="website">WWW.PINECREST-PAVING.COM</div>
    <div class="estimate-bar">FREE ESTIMATES</div>
  </div>
</body>
</html>
```